Stage Design Company Business Card

We are looking to step up up our business card design for our team.

We are a Full service Design and Consultation company for Stage and TV with an emphasis in Theatrical Lighting.

We like our materials to be clean and modern with solid colors free of patterns and gradients. Our brand consists of 4 primary colors Purple, Black, Grey, and White. Provided is our Word Mark as well as our Symbol Logo.

We would like our cards to leave an impression beyond the information, show our attention to design and detail, and make our marks an easily recognized feature (together or apart) for our clients.

We need a warm approachable comfortable feel for some clients, and a professional flair for the board member type clients.

Attached are our brand elements, and our existing cards to give a sense of our style and a glipse at the information we provide on our cards.

Target Market(s)

broad client base from church leaders to high school teachers and architects.

Industry/Entity Type

Business

Contact Information for Business Card

We format our phone number with periods not parenthesis or dashes. Information will be edited for each of our team members, and team member specific cards are not part of this scope, but rather a template so to speak.

Font styles to use
Sans Serif

Colors
6b449b
ffffff
000000
333333
aaaaaa

Requirements
Must have
• Wordmark and logo mark present (does not need to exist on the same side of card)
• Brand Colors,
• Name, Phone, Email, Address.
• Unique choices that make someone stop and take a second look
Nice to have
• It would be nice to somehow convey what we DO, as our brand name does not lend itself to this, outside of an obvious tagline though.....
• social media if not crowded. all of our handles match (instagram, twitter, facebook)
Should not have
• "clipart"

```html
<!DOCTYPE html>
<html lang="en">
<head>
<meta charset="utf-8">
<title>Calder Entertainment — Business Card</title>
<link rel="stylesheet" href="https://fonts.googleapis.com/css2?family=Michroma&display=swap">
<style>
  :root {
    --page-bg: #e6e6e6;
    --card-dark: #121826;
    --card-light: #f7f7f7;
    --ink-light: #ffffff;
    --ink-dark: #000000;
    --brand-purple: #6b449b;
    --brand-grey: #aaaaaa;
    --shadow: rgba(0, 0, 0, 0.18);
  }

  * { margin: 0; padding: 0; box-sizing: border-box; }

  html, body {
    width: 1200px;
    height: 900px;
    overflow: hidden;
  }

  body {
    background: var(--page-bg);
    font-family: "Michroma", sans-serif;
    display: flex;
    align-items: center;
    justify-content: center;
    gap: 120px;
  }

  .card {
    width: 340px;
    height: 595px;
    box-shadow: 0 10px 30px var(--shadow);
    display: flex;
    flex-direction: column;
    align-items: center;
    text-align: center;
  }

  /* Back: contact details */
  .card--contact {
    background: var(--card-dark);
    color: var(--ink-light);
    justify-content: center;
    gap: 34px;
    padding-bottom: 20px;
  }

  .contact__name {
    font-size: 20px;
    letter-spacing: 0.04em;
    text-transform: uppercase;
  }

  .contact__phone {
    font-size: 17px;
    letter-spacing: 0.02em;
  }

  .contact__email {
    font-size: 14px;
    letter-spacing: 0.02em;
  }

  .contact__address {
    font-style: normal;
    font-size: 15px;
    line-height: 1.45;
    text-transform: uppercase;
    letter-spacing: 0.03em;
  }

  /* Front: brand lockup */
  .card--brand {
    background: var(--card-light);
    justify-content: center;
    padding-bottom: 40px;
  }

  .brand__dot {
    width: 96px;
    height: 96px;
    border-radius: 50%;
    background: var(--brand-purple);
    margin-bottom: 44px;
  }

  .brand__name {
    font-size: 28px;
    color: var(--ink-dark);
    letter-spacing: 0.42em;
    margin-right: -0.42em;
    text-transform: uppercase;
  }

  .brand__tagline {
    margin-top: 14px;
    font-size: 9px;
    color: var(--brand-grey);
    letter-spacing: 0.72em;
    margin-right: -0.72em;
    text-transform: uppercase;
  }

  .brand__url {
    margin-top: 12px;
    font-size: 14px;
    color: var(--brand-purple);
    letter-spacing: 0.3em;
    margin-right: -0.3em;
    text-transform: uppercase;
  }
</style>
</head>
<body>

  <section class="card card--contact" aria-label="Card back with contact details">
    <h1 class="contact__name">Owen R Calder</h1>
    <p class="contact__phone">480.555.0142</p>
    <p class="contact__email">owen@calder-e.com</p>
    <address class="contact__address">214 N Pine St<br>Tempe, AZ 85281</address>
  </section>

  <section class="card card--brand" aria-label="Card front with brand name">
    <div class="brand__dot"></div>
    <p class="brand__name">Calder</p>
    <p class="brand__tagline">Entertainment</p>
    <p class="brand__url">calder-e.com</p>
  </section>

</body>
</html>
```